Business card for my new company (Accounting firm)

I need a business card for my new business Brightwell Advisory and Ledger SA. Our services are accounting, tax, audit and financial management. Our customers are small companies, start-ups and new companies. The final design has to show financial security, trust and growth. Please find our logo attached to the business card. Text for the business card: Brightwell Advisory and Ledger SA Tomas Varenholt Director and Founder Certified Accountant Tel. 022 418 57 34 tv@clairevalconseil.ch www.clairevalconseil.ch Rue des Vergières 27 1201 Geneva
Target Market(s)
Our customers are small companies, start-ups and new companies.
Industry/Entity Type
Finance And Accounting
Contact Information for Business Card
Claireval Conseil et Comptes SA
Tomas Varenholt
Directeur et Fondateur
Expert-comptable diplômé
Tél. 022 418 57 34
tv@clairevalconseil.ch
www.clairevalconseil.ch
Rue des Vergières 27
1201 Genève

```html
<!DOCTYPE html>
<html lang="fr">
<head>
<meta charset="utf-8">
<title>Claireval Conseil et Comptes SA – Carte de visite</title>
<link rel="stylesheet" href="https://fonts.googleapis.com/css2?family=Roboto:wght@400;500;700&display=swap">
<style>
  :root {
    --backdrop: #e3e4e6;
    --paper: #ffffff;
    --ink: #3a3b3d;
    --ink-soft: #55575a;
    --blue-light: #2ba3d8;
    --blue-mid: #1f7db8;
    --blue-deep: #175a8a;
    --name-blue: #1d6aa8;
  }
  * { box-sizing: border-box; margin: 0; padding: 0; }
  html, body { width: 1200px; height: 726px; overflow: hidden; }
  body {
    background: var(--backdrop);
    font-family: "Roboto", Arial, sans-serif;
    position: relative;
  }
  .card {
    position: absolute;
    top: 210px;
    width: 520px;
    height: 306px;
    background: var(--paper);
    box-shadow: 0 10px 28px rgba(0,0,0,0.14);
    overflow: hidden;
  }
  .card--front { left: 50px; }
  .card--back { left: 630px; }

  /* Front */
  .front-brand {
    position: absolute;
    left: 0; right: 0; top: 96px;
    display: flex;
    flex-direction: column;
    align-items: center;
    gap: 8px;
  }
  .brand-dot {
    width: 30px; height: 30px;
    background: var(--blue-mid);
  }
  .brand-name {
    font-family: "Roboto", Arial, sans-serif;
    font-weight: 500;
    color: var(--ink);
    text-transform: uppercase;
    letter-spacing: 0.16em;
    text-align: center;
    line-height: 1.25;
  }
  .front-brand .brand-name { font-size: 19px; }
  .front-stripe {
    position: absolute;
    left: 0; bottom: 0;
    width: 100%; height: 90px;
  }

  /* Back */
  .back-deco {
    position: absolute;
    left: 0; bottom: 0;
    width: 190px; height: 150px;
  }
  .back-content {
    position: absolute;
    right: 30px; top: 28px;
    text-align: right;
  }
  .back-content .brand-name {
    font-size: 17px;
    letter-spacing: 0.14em;
    margin-bottom: 20px;
  }
  .person-name {
    font-weight: 700;
    font-size: 17px;
    color: var(--name-blue);
    margin-bottom: 2px;
  }
  .person-role {
    font-size: 11px;
    color: var(--ink-soft);
    line-height: 1.35;
  }
  .contact-list {
    list-style: none;
    margin-top: 12px;
    font-size: 11.5px;
    color: var(--ink);
    line-height: 1.6;
  }
  .contact-list li {
    display: flex;
    justify-content: flex-end;
    align-items: center;
    gap: 7px;
  }
  .contact-icon { width: 11px; height: 11px; flex: none; }
  .contact-list .no-icon { padding-right: 18px; }
</style>
</head>
<body>

  <section class="card card--front" aria-label="Recto de la carte">
    <div class="front-brand">
      <span class="brand-dot" aria-hidden="true"></span>
      <p class="brand-name">Claireval<br>Conseil et Comptes</p>
    </div>
    <svg class="front-stripe" viewBox="0 0 520 90" preserveAspectRatio="none" aria-hidden="true">
      <polygon points="0,78 520,8 520,14 0,84" fill="var(--blue-light)"/>
      <polygon points="0,84 520,14 520,18 0,88" fill="var(--blue-mid)"/>
    </svg>
  </section>

  <section class="card card--back" aria-label="Verso de la carte">
    <svg class="back-deco" viewBox="0 0 190 150" aria-hidden="true">
      <rect x="-30" y="40" width="140" height="140" fill="var(--blue-deep)"/>
    </svg>

    <div class="back-content">
      <p class="brand-name">Claireval<br>Conseil et Comptes</p>
      <p class="person-name">Tomas Varenholt</p>
      <p class="person-role">Directeur et Fondateur<br>Expert-comptable diplômé</p>
      <ul class="contact-list">
        <li>022 418 57 34
          <svg class="contact-icon" viewBox="0 0 12 12" aria-hidden="true"><path d="M2.5 1 4.5 1 5 3.5 3.8 4.4C4.4 5.8 5.6 7.2 7.3 8L8.4 6.8 11 7.4 11 9.4C11 10.3 10.3 11 9.4 11 5 11 1 7 1 2.6 1 1.7 1.7 1 2.5 1Z" fill="var(--name-blue)"/></svg>
        </li>
        <li>tv@clairevalconseil.ch
          <svg class="contact-icon" viewBox="0 0 12 12" aria-hidden="true"><rect x="0.5" y="2" width="11" height="8" fill="var(--name-blue)"/><path d="M0.8 2.4 6 6.6 11.2 2.4" fill="none" stroke="#fff" stroke-width="1"/></svg>
        </li>
        <li>www.clairevalconseil.ch
          <svg class="contact-icon" viewBox="0 0 12 12" aria-hidden="true"><circle cx="6" cy="6" r="5.2" fill="var(--name-blue)"/><path d="M1 6H11M6 1C4 3 4 9 6 11M6 1C8 3 8 9 6 11" fill="none" stroke="#fff" stroke-width="0.8"/></svg>
        </li>
        <li class="no-icon">Rue des Vergières 27 1201 Genève</li>
      </ul>
    </div>
  </section>

</body>
</html>
```